Vento Hallmark Real estate Costa del sol

we need a website for our Company based in Costa del sol, Spain. We sell properties on the spanish coast that is called costa del sol. We are concentrating on exclusive properties and would like the webdesign to show this. In our website we want to have area descriptions of the different areas we sell our Products. We will also implement a searchable database delivered by a third part where all properties for sale in Spain are listed. When looking into the designs we would like our main page to have a overview of the coast where the different areas are shown. Have a look at brightlunavista.example or oakterra.example to see. The webpage will be presented in 4 languages, English, spanish, Swedish and norwegian, and shall of course also be prepared for social medias. We want an easy Contemporary design but still with an exclusive feeling!
Scandinavian and North european Citizens wants to buy a property in Spain
Real Estate
5+ page

```html
<!DOCTYPE html>
<html lang="en">
<head>
<meta charset="utf-8">
<title>Vento Hallmark – Real Estate Costa del Sol</title>
<link rel="stylesheet" href="https://fonts.googleapis.com/css2?family=Oswald:wght@400;500;600&family=Open+Sans:wght@400;600;700&display=swap">
<style>
:root{
  --navy:#1f2b4f;
  --navy-dark:#17203b;
  --ink:#2b2b2b;
  --muted:#777;
  --line:#d9d9d9;
  --soft:#f1f1f1;
  --footer:#2a2a2a;
  --footer-deep:#1d1d1d;
  --white:#fff;
}
*{box-sizing:border-box;margin:0;padding:0}
html,body{width:1200px;height:2940px;overflow:hidden}
body{font-family:"Open Sans",Arial,sans-serif;color:var(--ink);background:var(--white);position:relative;font-size:13px}
.abs{position:absolute}
h2.section-title{font-family:"Oswald",Arial,sans-serif;font-weight:500;font-size:30px;color:var(--navy);text-transform:uppercase;display:flex;align-items:center;letter-spacing:.5px;line-height:1.2}

/* header */
.header{position:absolute;left:0;top:0;width:1200px;height:88px;border-bottom:1px solid var(--line)}
.topstrip{position:absolute;right:40px;top:0;height:26px;width:370px;background:var(--navy-dark);display:flex;align-items:center;justify-content:flex-end;gap:14px;padding-right:14px;color:#fff;font-size:11px}
.topstrip .dot{width:10px;height:10px;background:#fff;opacity:.8;display:block}
.logo{position:absolute;left:104px;top:30px;display:flex;align-items:center;gap:8px}
.logo .square{width:14px;height:14px;background:var(--navy);display:block}
.logo span{font-family:"Open Sans",sans-serif;font-weight:700;font-size:16px;color:var(--navy)}
.nav{position:absolute;right:40px;top:46px;display:flex;gap:4px}
.nav a{font-size:14px;color:var(--ink);text-decoration:none;padding:10px 18px;line-height:1.4}
.nav a.active{background:var(--navy);color:#fff}

/* hero */
.hero{position:absolute;left:0;top:88px;width:1200px;height:384px;background:linear-gradient(180deg,#55697f 0%,#7d8894 40%,#3c3f3a 78%,#1f2620 100%)}
.hero-copy{position:absolute;left:240px;top:200px;color:#fff}
.hero-copy small{font-size:12px;letter-spacing:1px;text-transform:uppercase}
.hero-copy h1{font-family:"Open Sans",sans-serif;font-weight:700;font-size:32px;line-height:1.2;margin:6px 0 18px}
.btn{display:inline-block;background:var(--navy);color:#fff;font-size:12px;padding:9px 18px}
.arrow{position:absolute;top:200px;width:40px;height:60px}
.dots{position:absolute;display:flex;gap:8px}
.dots i{width:10px;height:10px;border-radius:50%;background:#bbb;display:block}
.dots i.on{background:var(--navy)}

/* search */
.search-tabs{position:absolute;left:0;top:472px;width:1200px;height:48px;background:var(--navy)}
.search-tabs .tab{position:absolute;top:0;height:48px;display:flex;align-items:center;gap:10px;color:#fff;font-size:17px}
.search-form{position:absolute;left:180px;top:600px;width:840px}
.row{display:flex;gap:30px;margin-bottom:26px}
.select{flex:1;height:38px;border-bottom:1px solid var(--line);display:flex;align-items:center;justify-content:space-between;font-size:12px;color:#555}
.select:after{content:"";width:0;height:0;border:5px solid transparent;border-top-color:#555;margin-top:5px}
.select.short{flex:0 0 180px}
.search-btn{margin-left:auto;background:var(--navy-dark);color:#fff;font-size:13px;width:270px;height:38px;display:flex;align-items:center;justify-content:center;gap:10px}

/* developments */
.developments{position:absolute;left:0;top:820px;width:1200px;height:400px;background:var(--soft)}
.view-all{position:absolute;right:160px;top:50px;display:flex;gap:2px}
.view-all span{background:var(--navy);color:#fff;font-size:11px;padding:6px 10px}
.view-all span.light{background:#ccc}
.cards{position:absolute;left:160px;top:120px;display:flex;gap:20px}
.card{width:205px;background:#fff}
.card .photo{height:110px}
.card .body{padding:12px 10px;height:120px}
.card h3{font-size:13px;font-weight:700;color:var(--navy);margin-bottom:6px}
.card p{font-size:11px;color:var(--muted);line-height:1.5}
.card .price{font-weight:700;color:var(--ink);font-size:13px;margin-top:8px}
.card .stats{height:30px;background:var(--navy);display:flex;justify-content:space-around;align-items:center;color:#fff;font-size:10px}

/* promoted */
.promoted{position:absolute;left:0;top:1240px;width:1200px;height:640px}
.caption{font-size:12px;color:var(--muted);text-align:center}
.promo{position:absolute;color:#fff}
.promo .label{position:absolute;left:16px;bottom:14px;right:16px;display:flex;justify-content:space-between;align-items:flex-end}
.promo .label b{font-family:"Open Sans",sans-serif;font-weight:600;font-size:18px;display:block}
.promo .label em{font-style:normal;font-size:11px}
.promo .price{background:rgba(255,255,255,.15);font-weight:700;font-size:16px;padding:3px 8px}

/* testimonials */
.testimonials{position:absolute;left:0;top:1900px;width:1200px;height:370px;background:linear-gradient(180deg,#2a2a2e,#1c1d22)}
.testimonials h2.section-title{color:#fff}
.avatar{position:absolute;left:160px;width:56px;height:56px;background:#6a6a6a;border:2px solid #fff}
.quote-box{position:absolute;left:260px;top:132px;width:772px;height:198px;border:1px solid rgba(255,255,255,.25);color:#ddd;text-align:center;padding:20px 40px}
.quote-box .mark{font-family:Georgia,serif;font-size:54px;line-height:40px;color:#fff}
.quote-box p{font-size:12px;line-height:1.7;margin:8px 0 12px}
.quote-box .who{font-family:Georgia,serif;font-style:italic;color:#fff;font-size:14px}

/* clients */
.clients{position:absolute;left:0;top:2280px;width:1200px;height:260px}
.clients .intro{position:absolute;left:300px;width:600px;top:92px;font-size:12px;color:var(--muted);text-align:center;line-height:1.6}
.client-row{position:absolute;left:152px;top:140px;width:896px;display:flex;align-items:center;gap:8px}
.client{flex:1;height:72px;border:1px solid var(--line);display:flex;align-items:center;justify-content:center;font-family:"Open Sans",sans-serif;font-weight:700;font-size:14px;color:#333;white-space:nowrap}
.client-arrow{width:18px;height:18px;background:var(--navy);display:block}
.pager{position:absolute;left:582px;top:232px;display:flex;gap:4px}
.pager span{width:18px;height:18px;font-size:11px;display:flex;align-items:center;justify-content:center;background:#ccc;color:#fff}
.pager span.on{background:var(--navy)}

/* footer */
.footer{position:absolute;left:0;top:2560px;width:1200px;height:340px;background:var(--footer);color:#bbb}
.footer h4{font-family:"Open Sans",sans-serif;font-weight:600;color:#fff;font-size:17px;margin-bottom:22px}
.footer .col{position:absolute;top:52px}
.footer-brand{display:flex;align-items:center;gap:8px;font-weight:700;font-size:17px;color:#fff}
.footer-brand i{width:14px;height:14px;background:#fff;display:block}
.footer p{font-size:12px;line-height:1.7}
.social{display:flex;gap:8px;margin-top:22px}
.social i{width:26px;height:26px;background:#444;display:block}
.contact-line{display:flex;gap:10px;font-size:12px;margin-bottom:14px;line-height:1.5}
.contact-line svg{flex:0 0 14px;margin-top:2px}
.cities{display:flex;gap:60px}
.cities ul{list-style:none}
.cities li{font-size:12px;margin-bottom:8px}
.cities li:before{content:"› ";color:#fff}
.bottom-bar{position:absolute;left:0;top:2900px;width:1200px;height:40px;background:var(--footer-deep);color:#999;font-size:11px}
.bottom-bar .copy{position:absolute;left:160px;top:13px}
.bottom-bar .links{position:absolute;right:160px;top:13px;display:flex;gap:18px}
.bottom-bar .links .on{color:#fff}
</style>
</head>
<body>

<header class="header">
  <div class="topstrip">
    <i class="dot"></i><i class="dot"></i><i class="dot"></i><i class="dot"></i>
    <span>Tel: +34 952 000 118</span>
  </div>
  <div class="logo"><i class="square"></i><span>Vento Hallmark</span></div>
  <nav class="nav">
    <a class="active">Home</a><a>About Us</a><a>Costa del Sol</a><a>Service</a><a>Testimonial</a><a>Contact Us</a>
  </nav>
</header>

<section class="hero" role="img" aria-label="Photo of a large family house with garage at dusk">
  <svg class="arrow" style="left:40px" viewBox="0 0 40 60"><path d="M28 8 L10 30 L28 52" stroke="#fff" stroke-width="3" fill="none"/></svg>
  <svg class="arrow" style="right:40px" viewBox="0 0 40 60"><path d="M12 8 L30 30 L12 52" stroke="#fff" stroke-width="3" fill="none"/></svg>
  <div class="hero-copy">
    <small>We Always Have Your Home</small>
    <h1>We Are Always Here To<br>Fullfil Your Dreams</h1>
    <span class="btn">Read More</span>
  </div>
  <div class="dots" style="left:572px;top:340px"><i></i><i class="on"></i><i></i></div>
</section>

<div class="search-tabs">
  <div class="tab" style="left:200px">
    <svg width="18" height="18" viewBox="0 0 18 18"><circle cx="7" cy="7" r="5" stroke="#fff" stroke-width="2" fill="none"/><path d="M11 11 L16 16" stroke="#fff" stroke-width="2"/></svg>Find Your Home
  </div>
  <div class="tab" style="left:420px">
    <svg width="18" height="18" viewBox="0 0 18 18"><path d="M2 9 L9 2 L16 9 V16 H2 Z" fill="#fff"/></svg>Home for sell
  </div>
</div>

<form class="search-form">
  <div class="row"><div class="select">Location</div><div class="select">Sub Location</div><div class="select">Status</div></div>
  <div class="row"><div class="select">No.of Bedrooms</div><div class="select">No.of Bathrooms</div><div class="select">No.of Parkings</div></div>
  <div class="row">
    <div class="select short">Min.of Bathrooms</div>
    <div class="select short">Price (USD 100k)</div>
    <div class="search-btn">
      <svg width="14" height="14" viewBox="0 0 18 18"><circle cx="7" cy="7" r="5" stroke="#fff" stroke-width="2" fill="none"/><path d="M11 11 L16 16" stroke="#fff" stroke-width="2"/></svg>Search Property
    </div>
  </div>
</form>

<section class="developments">
  <h2 class="section-title abs" style="left:160px;top:48px">New Developments</h2>
  <div class="view-all"><span class="light">‹</span><span>View All</span><span class="light">›</span></div>
  <div class="cards">
    <article class="card">
      <div class="photo" role="img" aria-label="Photo of a modern villa" style="background:linear-gradient(#6f86a3,#4a5a4d)"></div>
      <div class="body"><h3>EL Pehalk Mountain Villa</h3><p>Bright villa with sea views and a private garden.</p><div class="price">$ 180,000</div></div>
      <div class="stats"><span>3 Bed</span><span>2 Bath</span><span>1 Park</span><span>240 m²</span></div>
    </article>
    <article class="card">
      <div class="photo" role="img" aria-label="Photo of an interior living room" style="background:linear-gradient(#3a3a3a,#6a5c4c)"></div>
      <div class="body"><h3>EL Pehalk Mountain Villa</h3><p>Open living area close to the golf and beach.</p><div class="price">$ 210,000</div></div>
      <div class="stats"><span>4 Bed</span><span>3 Bath</span><span>2 Park</span><span>310 m²</span></div>
    </article>
    <article class="card">
      <div class="photo" role="img" aria-label="Photo of a house with lawn" style="background:linear-gradient(#8ea7c6,#5d7a4a)"></div>
      <div class="body"><h3>EL Pehalk Mountain Villa</h3><p>Family home on a quiet street near the old town.</p><div class="price">$ 165,000</div></div>
      <div class="stats"><span>3 Bed</span><span>2 Bath</span><span>1 Park</span><span>200 m²</span></div>
    </article>
    <article class="card">
      <div class="photo" role="img" aria-label="Photo of a townhouse" style="background:linear-gradient(#9bb3cf,#6c6f6a)"></div>
      <div class="body"><h3>EL Pehalk Mountain Villa</h3><p>Townhouse with terrace and shared pool area.</p><div class="price">$ 142,000</div></div>
      <div class="stats"><span>2 Bed</span><span>2 Bath</span><span>1 Park</span><span>150 m²</span></div>
    </article>
  </div>
</section>

<section class="promoted">
  <p class="caption abs" style="left:0;width:1200px;top:50px">Find Property In Your City</p>
  <h2 class="section-title abs" style="left:0;width:1200px;top:74px;justify-content:center">Specially Promoted</h2>
  <div class="promo" role="img" aria-label="Photo of a luxury villa at dusk" style="left:160px;top:148px;width:432px;height:360px;background:linear-gradient(#7f97b8,#55604f 70%,#3a3f33)">
    <div class="label"><div><b>Luxury Villa</b><em>12 Properties</em></div><span class="price">$132,000</span></div>
  </div>
  <div class="promo" role="img" aria-label="Photo of a swimming pool at night" style="left:608px;top:148px;width:432px;height:200px;background:linear-gradient(#1e2a44,#2f3d55 55%,#c49a5a)">
    <div class="label"><div><b>Swimming Pool</b><em>22 Properties</em></div><span class="price">$143,000</span></div>
  </div>
  <div class="promo" role="img" aria-label="Photo of a city garden home" style="left:608px;top:360px;width:204px;height:148px;background:linear-gradient(#6d8099,#4c5848)">
    <div class="label"><div><b style="font-size:14px">City Garden</b><em>8 Properties</em></div><span class="price" style="font-size:12px">$132,000</span></div>
  </div>
  <div class="promo" role="img" aria-label="Photo of a house with garden" style="left:828px;top:360px;width:212px;height:148px;background:linear-gradient(#8fa5bf,#5a6350)">
    <div class="label"><div><b style="font-size:14px">Garden</b><em>14 Properties</em></div><span class="price" style="font-size:12px">$132,000</span></div>
  </div>
  <div class="dots" style="left:570px;top:534px"><i class="on"></i><i></i><i></i><i></i></div>
</section>

<section class="testimonials" role="img" aria-label="Dark photo background of a lit home at night">
  <h2 class="section-title abs" style="left:0;width:1200px;top:50px;justify-content:center">Clients Testimonials</h2>
  <div class="avatar" style="top:146px"></div>
  <div class="avatar" style="top:214px"></div>
  <div class="avatar" style="top:282px"></div>
  <div class="quote-box">
    <div class="mark">“</div>
    <p>We found our dream home on the coast with friendly help from start to finish. The team knew every area well and guided us through each step of the purchase, from the first viewing to the final signing. We felt safe, informed and welcome all along the way, and we can truly recommend their service to anyone looking for a quality home in the sun.</p>
    <div class="who">- Mr. Anders Holm, Company Name</div>
  </div>
  <svg class="abs" style="left:1048px;top:216px" width="14" height="24" viewBox="0 0 14 24"><path d="M2 2 L12 12 L2 22" stroke="#fff" stroke-width="2" fill="none"/></svg>
</section>

<section class="clients">
  <h2 class="section-title abs" style="left:0;width:1200px;top:40px;justify-content:center">Our Valued Clients</h2>
  <p class="intro">We work with trusted partners across the coast to give buyers a smooth and secure journey to their new home.</p>
  <div class="client-row">
    <i class="client-arrow"></i>
    <div class="client">Rivenco</div>
    <div class="client">Linden Works</div>
    <div class="client">Meadowbright</div>
    <div class="client">Paperfield</div>
    <div class="client">Korvale</div>
    <div class="client">Tidewire</div>
    <div class="client">Linden Works</div>
    <i class="client-arrow"></i>
  </div>
  <div class="pager"><span class="on">1</span><span>2</span></div>
</section>

<footer class="footer">
  <div class="col" style="left:160px;width:250px">
    <div class="footer-brand"><i></i>Vento Hallmark</div>
    <p style="margin-top:26px">We help families from the north find their home on the sunny Spanish coast, with care and local knowledge at every step of the way.</p>
    <div class="social"><i></i><i></i><i></i><i></i></div>
  </div>
  <div class="col" style="left:528px;width:230px">
    <h4>Get In Touch</h4>
    <div class="contact-line"><svg width="14" height="16" viewBox="0 0 14 16"><path d="M7 1 C3 1 1 4 1 6 C1 10 7 15 7 15 C7 15 13 10 13 6 C13 4 11 1 7 1Z" fill="#bbb"/></svg><span><b style="color:#fff">VENTO HALLMARK</b><br>Avenida del Mar 12, 29600 Marbella, Málaga</span></div>
    <div class="contact-line"><svg width="14" height="14" viewBox="0 0 14 14"><path d="M3 1 L5 4 L4 6 C5 8 6 9 8 10 L10 9 L13 11 L12 13 C6 13 1 8 1 2Z" fill="#bbb"/></svg><span>+34 952 000 118</span></div>
    <div class="contact-line"><svg width="14" height="12" viewBox="0 0 14 12"><rect x="1" y="1" width="12" height="10" fill="none" stroke="#bbb" stroke-width="1.5"/><path d="M1 1 L7 7 L13 1" stroke="#bbb" stroke-width="1.5" fill="none"/></svg><span>info@ventohallmark.example</span></div>
  </div>
  <div class="col" style="left:800px;width:260px">
    <h4>Property Cities</h4>
    <div class="cities">
      <ul><li>Estepona</li><li>Marbella</li><li>Benahavís</li><li>Mijas</li><li>Fuengirola</li><li>Nerja</li></ul>
      <ul><li>Manilva</li><li>Benalmádena</li><li>Torremolinos</li><li>Casares</li><li>Málaga</li><li>Ojén</li></ul>
    </div>
  </div>
</footer>

<div class="bottom-bar">
  <span class="copy">© Copyright 2016, Vento Hallmark. All Right Reserved.</span>
  <div class="links"><span>Home</span><span class="on">About Us</span><span>Costa del Sol</span><span>Service</span><span>Testimonial</span><span>Contact Us</span></div>
</div>

</body>
</html>
```